Professional & attention grabbing.

A business card design, front and back. I already have a logo I will attach, but I am open to something new as well.
Things to include:
Name:
Title:
Phone:
Email:
Wanting something that is professional but attention grabbing.
Also we do a lot of work using drones on natural gas pipelines (leading the future)if you want to include any of that. I'm open to ideas.
Target Market(s)
Natural gas transmission industry / greenhouse gas mitigation industry
Industry/Entity Type
Business
Colors
Designer to choose colors to be used in the design.
Look and feel
Each slider illustrates characteristics of the customer's brand and the style your logo design should communicate.

```html
<!DOCTYPE html>
<html lang="en">
<head>
<meta charset="utf-8">
<title>Kestrel Inspection – Business Card</title>
<link rel="stylesheet" href="https://fonts.googleapis.com/css2?family=Open+Sans:wght@400;600;700&display=swap">
<style>
  :root {
    --backdrop: #3b3431;
    --card: #111111;
    --orange: #f07d14;
    --silver: #b9b9b9;
    --grey: #8f8f8f;
    --white: #f2f2f2;
  }
  * { box-sizing: border-box; margin: 0; padding: 0; }
  html, body {
    width: 1200px; height: 900px; overflow: hidden;
    background: var(--backdrop);
    font-family: "Open Sans", Arial, sans-serif;
  }
  .canvas {
    position: relative; width: 1200px; height: 900px;
    display: flex; align-items: center; justify-content: center; gap: 40px;
  }
  .card {
    width: 500px; height: 286px;
    background: var(--card);
    border-radius: 3px;
    box-shadow: 0 14px 30px rgba(0,0,0,.45);
    position: relative;
  }
  /* Front */
  .card--front { display: flex; align-items: center; }
  .brand {
    width: 250px; display: flex; align-items: center; justify-content: center; gap: 10px;
  }
  .brand__square { width: 16px; height: 16px; background: var(--orange); }
  .brand__name {
    font-weight: 700; font-size: 20px; letter-spacing: .5px; text-transform: uppercase;
  }
  .card--front .brand__name { color: var(--grey); }
  .divider {
    width: 1px; height: 130px;
    background: linear-gradient(to bottom, transparent, var(--orange) 30%, var(--orange) 70%, transparent);
  }
  .contact { padding-left: 28px; color: var(--white); }
  .contact__name {
    color: var(--orange); font-weight: 600; font-size: 19px; text-transform: uppercase; line-height: 1.1;
  }
  .contact__title { font-size: 13px; margin-bottom: 14px; }
  .contact__row { display: flex; align-items: center; gap: 8px; font-size: 13px; line-height: 1.6; }
  .contact__row svg { width: 10px; height: 10px; fill: var(--orange); flex: none; }
  .contact__address { font-size: 14px; line-height: 1.35; margin-top: 14px; }
  /* Back */
  .card--back { display: flex; align-items: center; justify-content: center; }
  .card--back .brand { width: auto; gap: 14px; }
  .card--back .brand__square { width: 24px; height: 24px; background: var(--silver); }
  .card--back .brand__name { color: var(--silver); font-size: 30px; }
</style>
</head>
<body>
  <main class="canvas">
    <section class="card card--front" aria-label="Card front">
      <div class="brand">
        <span class="brand__square"></span>
        <span class="brand__name">Kestrel Inspection</span>
      </div>
      <div class="divider"></div>
      <div class="contact">
        <p class="contact__name">Marcus Hale</p>
        <p class="contact__title">Managing Director</p>
        <p class="contact__row">
          <svg viewBox="0 0 10 10" aria-hidden="true"><path d="M2 0.5 L3.6 2.6 L2.7 3.6 Q3.7 5.8 6.4 7.3 L7.4 6.4 L9.5 8 L8.4 9.5 Q3.5 9 0.5 1.6 Z"/></svg>
          (044)987654321
        </p>
        <p class="contact__row">
          <svg viewBox="0 0 10 10" aria-hidden="true"><path d="M0.5 2 H9.5 V8.5 H0.5 Z M0.5 2 L5 5.5 L9.5 2" stroke="#111" stroke-width=".7"/></svg>
          info@kestrelinspect.com
        </p>
        <p class="contact__address">48 Ridgeway Lane, Unit 7<br>Northfield, 204518.</p>
      </div>
    </section>
    <section class="card card--back" aria-label="Card back">
      <div class="brand">
        <span class="brand__square"></span>
        <span class="brand__name">Kestrel Inspection</span>
      </div>
    </section>
  </main>
</body>
</html>
```